Start-Up für Training, Coaching & Consulting sucht modernes Webdesign!
Zielgruppe
Wer ist TAVI Training, Coaching & Consulting?
Wir führen Führungskräftetrainings durch, machen Privatkunden für Bewerbungen fit und unterstützen Unternehmen mit Verkaufstrainings. Wir entwickeln Persönlichkeiten im Coaching. Wir beraten Unternehmen und helfen ihnen dabei, ihre Geschäftsabläufe und Prozesse zu optimieren. Dabei steht unsere hohe Qualität im Mittelpunkt - gemeinsam mit unseren kreativen Trainingsmethoden. Unser Background (Diplom-Kaufleute und geprüfte Trainer) bietet dafür die passende Ausgangslage.
Was bedeutet TAVI?
Tavi ist Maori und bdeutet Kreis/Spirale. Er symbolisiert einen wachsenden Silberfarn und steht für persönliche Entwicklung und Entfaltung. Der Tavi ist einerseits unser Namensgeber und unser Logo, andererseits steht der Tavi aber auch für unsere Werte: Denn wir wollen unseren Kunden dabei helfen zu wachsen und sich weiterzuentwickeln - und dies auf eine hochqualitative und seriöse Art und Weise ohne den Eindruck von Esoterik oder Erlebnispädagogik zu vermitteln.
Aufgabenstellung
Modernes Design, das unsere Philosophie widerspiegelt: Wir möchten unseren Kunden auf seriöse und hochqualitative Weise weiterentwickeln. Wir stehen für nachhaltigen Lernerfolg, kreative Trainingsmethoden, Abwechslung, Spaß am Lernen, Qualität, Kompetenz, Fachwissen und Dynamik.
Layout:
1) Header: QMSR geprüfter Trainer, Menüpunkte (siehe Architektur)
2) Banner
3) 3 Teaser (Training, Coaching, Consulting) + Header + 2-3 Zeilen Text (+Icons)
>>> Sichtbarer Bereich auf Homepage: Menü, Banner, Teaser
4) "Warum Sie uns wählen sollten": 5 bullet points ohne weiteren Text
5) "Aus unserem Blog": Frame für 3 Blogartikel + Bild + Datum + Header + 2-3 Zeilen Text
6) Alle drei QMSR Logos
7) Footer: Click Us (quick links), Contact Us (Adresse), Follow Us (Pinnwald, ZOLP, Kontaktor)
8) Copyright + Impressum
>>> Das Design soll klar sein, aber nicht zu kantig. Vielmehr sollen abgerundete Ecken und dynamische Elemente genutzt werden.
Architektur:
3 Ebenen:
1) Homepage
2) TAVI, Training, Coaching, Consulting, für Trainer, Kundenstimmen/Referenzen, Kontakt
3) noch zu bestimmende Produktdetailseiten
Texte werden noch erstellt, Layout kann ggf. mit Platzhaltertext gefüllt werden.
Bildmaterial: Logo und vorhandenes Imagebild werden zur Verfügung gestellt. Bilder können ggf. gekauft werden. Vorschläge erwünscht.
Corporate colors:
grün: #a2c61b + monochromatic colors
http://www.tintoskop.de/a2c61b
grau: #474747 + monochromatic colors
http://www.tintoskop.de/474747

```html
<!DOCTYPE html>
<html lang="de">
<head>
<meta charset="utf-8">
<title>TAVI – Training, Coaching, Consulting</title>
<link href="https://fonts.googleapis.com/css2?family=Titillium+Web:wght@300;400;600&display=swap" rel="stylesheet">
<style>
:root{
  --green:#a2c61b;
  --green-dark:#8aab12;
  --grey:#474747;
  --grey-dark:#2b2b2b;
  --text:#333;
  --line:#cfcfcf;
  --white:#fff;
  --badge:#1d5fae;
}
*{margin:0;padding:0;box-sizing:border-box}
html,body{width:721px;height:1200px;overflow:hidden;background:var(--white)}
body{position:relative;font-family:"Titillium Web",sans-serif;color:var(--text);font-weight:300}
.abs{position:absolute}
/* header */
.site-header{left:0;top:0;width:721px;height:49px;background:var(--white)}
.brand{left:21px;top:11px;display:flex;align-items:center;gap:5px;font-size:20px;font-weight:600;color:var(--grey);letter-spacing:1px}
.brand .dot{width:12px;height:12px;border-radius:50%;background:var(--green)}
.brand-sub{left:21px;top:35px;font-size:5px;color:var(--grey);font-weight:400}
.nav a{position:absolute;top:17px;font-size:10.5px;color:var(--grey);text-decoration:none;font-weight:400}
.nav a.active{color:var(--green)}
.nav .active-bar{position:absolute;left:174px;top:46px;width:28px;height:3px;background:var(--green)}
.caret{font-size:8px;color:var(--green);margin-left:6px}
.cert-badge{left:640px;top:17px;width:59px;height:16px;background:var(--badge);border-radius:1px}
/* hero */
.hero{left:0;top:49px;width:721px;height:251px;background:radial-gradient(ellipse at 45% 45%,#9acb55 0%,#4f8a23 40%,#234d12 100%)}
.hero h1{position:absolute;left:73px;top:80px;font-size:22px;line-height:26px;font-weight:400;color:var(--white)}
.hero p{position:absolute;left:74px;top:144px;font-size:12px;line-height:14.5px;font-weight:400;color:var(--white)}
.hero svg{position:absolute;top:108px}
/* welcome */
.welcome-band{left:0;top:299px;width:721px;height:110px}
.welcome-title{left:0;top:318px;width:729px;text-align:center;font-size:18px;font-weight:400;color:var(--white)}
.welcome-sub{left:0;top:344px;width:729px;text-align:center;font-size:9.5px;color:var(--white);font-weight:400}
.teaser{top:379px;width:219px}
.teaser .photo{width:219px;height:117px;border:4px solid var(--green);border-top-width:0;background:linear-gradient(135deg,#b08d74,#d9cfc6 55,#8f6f5c)}
.teaser .photo.a{background:linear-gradient(120deg,#c6a38a,#e8ded6 45%,#a06e54)}
.teaser .photo.b{background:linear-gradient(120deg,#dde3ea,#f6f7f9 50%,#9aa6b2)}
.teaser .photo.c{background:linear-gradient(120deg,#8fa4b4,#dfe6ea 45%,#b9a48d)}
.teaser .icon{position:absolute;left:86px;top:84px;width:48px;height:48px;border-radius:50%;background:var(--white);border:4px solid var(--green)}
.teaser .icon svg{position:absolute;left:9px;top:9px}
.teaser h2{position:absolute;top:148px;width:219px;text-align:center;font-size:13px;font-weight:400;color:var(--green)}
.teaser p{position:absolute;top:170px;width:219px;text-align:center;font-size:7.7px;line-height:10.5px;color:var(--text);font-weight:400}
.teaser .btn{position:absolute;top:216px;left:72px;width:69px;height:21px;border-radius:2px;background:var(--green);color:var(--white);font-size:10px;line-height:21px;text-align:center;font-weight:400}
.rule{left:21px;width:679px;height:1px;background:var(--line)}
.rule.green{background:var(--green)}
/* why */
.why h3,.blog h3{font-size:13px;font-weight:400;color:var(--grey)}
.why{left:21px;top:680px;width:290px}
.why p{margin-top:3px;font-size:7.8px;line-height:10.5px;font-weight:400;color:var(--text)}
.why ul{list-style:none;margin:29px 0 0 37px}
.why li{font-size:10px;line-height:24px;color:var(--green);font-weight:400}
.why li::before{content:"• "}
.divider{left:360px;top:675px;width:1px;height:211px;background:var(--line)}
.blog{left:404px;top:680px;width:300px}
.post{position:absolute;left:0;width:300px;height:50px}
.post .thumb{position:absolute;left:0;top:0;width:49px;height:49px;border-radius:50%;border:3px solid var(--green);background:linear-gradient(135deg,#c9d6e4,#f2efe9 50%,#b68c6b)}
.post .date{position:absolute;left:59px;top:-2px;font-size:8.5px;color:var(--green);font-weight:400}
.post .title{position:absolute;left:59px;top:9px;font-size:8.5px;color:var(--grey);font-weight:400}
.post .excerpt{position:absolute;left:59px;top:25px;width:210px;font-size:6.4px;line-height:8.5px;color:var(--text);font-weight:400}
/* partners */
.partner{background:var(--badge);border-radius:1px}
/* footer */
.footer-shape{left:0;top:990px;width:721px;height:210px}
.footer-brand{left:27px;top:1054px;display:flex;align-items:center;gap:4px;font-size:17px;font-weight:600;color:var(--white);letter-spacing:1px}
.footer-brand .dot{width:10px;height:10px;border-radius:50%;background:var(--green)}
.fcol{top:1062px;color:var(--white);font-size:7.8px;line-height:10.5px;font-weight:400}
.fcol h4{font-size:8.5px;font-weight:600;margin-bottom:9px}
.social{display:flex;gap:8px}
.social span{width:15px;height:15px;border-radius:50%;background:var(--green)}
.copyright{left:29px;top:1176px;font-size:8px;color:var(--white);font-weight:400}
</style>
</head>
<body>

<header class="abs site-header">
  <div class="abs brand"><span>TAVI</span><span class="dot"></span></div>
  <div class="abs brand-sub">Training • Coaching • Consulting</div>
  <nav class="nav">
    <a class="active" style="left:166px">Startseite</a>
    <a style="left:246px">Leistungen<span class="caret">&#8744;</span></a>
    <a style="left:331px">Für Trainer<span class="caret">&#8744;</span></a>
    <a style="left:416px">Referenzen</a>
    <a style="left:503px">Kontakt</a>
    <span class="active-bar"></span>
  </nav>
  <div class="abs cert-badge" role="img" aria-label="Siegel geprüfter Business-Trainer"></div>
</header>

<section class="abs hero" role="img" aria-label="Foto eines sich entrollenden Farnwedels">
  <h1>Nachhaltiger Lernerfolg durch<br>kreative Trainingsmethoden</h1>
  <p>Wir helfen Ihnen dabei zu wachsen und<br>sich weiterzuentwickeln</p>
  <svg style="left:21px" width="22" height="24" viewBox="0 0 22 24"><path d="M17 2 L5 12 L17 22" fill="none" stroke="#fff" stroke-width="5"/></svg>
  <svg style="left:678px" width="22" height="24" viewBox="0 0 22 24"><path d="M5 2 L17 12 L5 22" fill="none" stroke="#fff" stroke-width="5"/></svg>
</section>

<svg class="abs welcome-band" viewBox="0 0 721 110" preserveAspectRatio="none">
  <path d="M0 0 H721 V90 Q700 88 690 84 L30 84 Q10 88 0 112 Z" fill="#a2c61b"/>
</svg>
<div class="abs welcome-title">Willkommen auf TAVI</div>
<div class="abs welcome-sub">Lorem ipsum dolor sit amet, consetetur sadipscing elitr</div>

<article class="abs teaser" style="left:22px">
  <div class="photo a" role="img" aria-label="Foto: Trainer mit Tablet vor Teilnehmenden"></div>
  <div class="icon"><svg width="22" height="22" viewBox="0 0 22 22"><circle cx="10" cy="6" r="5" fill="#111"/><path d="M1 21 Q2 12 10 12 Q16 12 17 16 V21 Z" fill="#111"/><path d="M18 15 V21 M15 18 H21" stroke="#111" stroke-width="1.5"/></svg></div>
  <h2>TRAINING</h2>
  <p>Lorem ipsum dolor sit amet, consetetur sadipscing elitr,<br>sed diam nonumy eirmod tempor invidunt ut labore et<br>dolore magna aliquyam erat, sed diam voluptua.</p>
  <div class="btn">Mehr</div>
</article>
<article class="abs teaser" style="left:251px">
  <div class="photo b" role="img" aria-label="Foto: Hände an einem Tablet beim Coaching"></div>
  <div class="icon"><svg width="22" height="22" viewBox="0 0 22 22"><rect x="9" y="2" width="11" height="8" fill="none" stroke="#111" stroke-width="1.3"/><circle cx="5" cy="4" r="2" fill="#111"/><rect x="3" y="7" width="4" height="7" fill="#111"/><circle cx="5" cy="17" r="2" fill="#111"/><circle cx="11" cy="17" r="2" fill="#111"/><circle cx="17" cy="17" r="2" fill="#111"/><rect x="2" y="19" width="18" height="3" fill="#111"/></svg></div>
  <h2>COACHING</h2>
  <p>Lorem ipsum dolor sit amet, consetetur sadipscing elitr,<br>sed diam nonumy eirmod tempor invidunt ut labore et<br>dolore magna aliquyam erat, sed diam voluptua.</p>
  <div class="btn">Mehr</div>
</article>
<article class="abs teaser" style="left:481px">
  <div class="photo c" role="img" aria-label="Foto: Beraterin im Gespräch mit einer Gruppe"></div>
  <div class="icon"><svg width="22" height="22" viewBox="0 0 22 22"><circle cx="6" cy="8" r="3.5" fill="#111"/><path d="M0 20 Q1 13 6 13 Q11 13 12 20 Z" fill="#111"/><circle cx="15" cy="5" r="3.5" fill="#111"/><path d="M10 15 Q11 9 15 9 Q20 9 21 15 Z" fill="#111"/></svg></div>
  <h2>CONSULTING</h2>
  <p>Lorem ipsum dolor sit amet, consetetur sadipscing elitr,<br>sed diam nonumy eirmod tempor invidunt ut labore et<br>dolore magna aliquyam erat, sed diam voluptua.</p>
  <div class="btn">Mehr</div>
</article>

<div class="abs rule" style="top:654px"></div>

<section class="abs why">
  <h3>Wählen Sie Uns</h3>
  <p>Lorem ipsum dolor sit amet, consetetur sadipscing elitr, sed diam nonumy eirmod tempor invidunt ut labore et dolore magna aliquyam erat, sed diam voluptua. At vero eos et accusam et justo duo dolores et ea rebum.</p>
  <ul>
    <li>Lorem ipsum dolor sit amet</li>
    <li>Lorem ipsum dolor sit amet</li>
    <li>Lorem ipsum dolor sit amet</li>
    <li>Lorem ipsum dolor sit amet</li>
    <li>Lorem ipsum dolor sit amet</li>
  </ul>
</section>

<div class="abs divider"></div>

<section class="abs blog">
  <h3>Unser Blog</h3>
  <div class="post" style="top:30px"><div class="thumb" role="img" aria-label="Blogbild: Seminargruppe"></div><div class="date">21.12.2015 - 12:48 Uhr</div><div class="title">Kreative Trainingsmethoden</div><div class="excerpt">Lorem ipsum dolor sit amet, consectetur adipisicing elit, sed do eiusmod tempor incididunt ut labore et dolore magna aliqua.</div></div>
  <div class="post" style="top:92px"><div class="thumb" role="img" aria-label="Blogbild: Seminargruppe"></div><div class="date">21.12.2015 - 12:48 Uhr</div><div class="title">Kreative Trainingsmethoden</div><div class="excerpt">Lorem ipsum dolor sit amet, consectetur adipisicing elit, sed do eiusmod tempor incididunt ut labore et dolore magna aliqua.</div></div>
  <div class="post" style="top:152px"><div class="thumb" role="img" aria-label="Blogbild: Seminargruppe"></div><div class="date">21.12.2015 - 12:48 Uhr</div><div class="title">Kreative Trainingsmethoden</div><div class="excerpt">Lorem ipsum dolor sit amet, consectetur adipisicing elit, sed do eiusmod tempor incididunt ut labore et dolore magna aliqua.</div></div>
</section>

<div class="abs rule green" style="top:911px"></div>

<div class="abs partner" style="left:196px;top:957px;width:80px;height:22px" role="img" aria-label="Partnersiegel geprüfter Business-Trainer"></div>
<div class="abs partner" style="left:335px;top:951px;width:25px;height:32px" role="img" aria-label="Partnersiegel Mitglied"></div>
<div class="abs partner" style="left:449px;top:951px;width:27px;height:34px" role="img" aria-label="Partnersiegel Berufsverband"></div>

<svg class="abs footer-shape" viewBox="0 0 721 210" preserveAspectRatio="none">
  <path d="M0 23 Q380 40 721 6 V210 H0 Z" fill="#2b2b2b"/>
</svg>
<div class="abs footer-brand"><span>TAVI</span><span class="dot"></span></div>
<div class="abs fcol" style="left:240px"><h4>Quicklinks</h4>Startseite<br>Referenzen<br>Kontakt<br>Impressum</div>
<div class="abs fcol" style="left:371px"><h4>Kontakt</h4>TAVI GmbH<br>Am Lindenhof 4<br>21450 Birkenfelde<br><br>Tel:&nbsp;&nbsp;&nbsp;040 55 21 907<br>E-Mail: info@tavi-beispiel.de</div>
<div class="abs fcol" style="left:494px"><h4>Folgen</h4>
  <div class="social"><span title="Pinnwald" aria-label="Pinnwald"></span><span title="Kontaktor" aria-label="Kontaktor"></span><span title="ZOLP" aria-label="ZOLP"></span></div>
</div>
<div class="abs copyright">© Copyright 2001-2016 - All Rights Reserved</div>

</body>
</html>
```